Brell Stone Company Business Cards

Front and Back Business Card - logo and text setup - cool design. I need workable photoshop or illustrator files so I can setup each employee card with design that is created
Updates

Hi everyone, thank you for the great entries. Please no more white and blue cards - there are so many already - black and silver only now please. thanks!

Target Market(s)

Construction Industry - Facility Managers

Industry/Entity Type

Construction

Contact Information for Business Card

I really like contemporary simplistic looks - clean neat....not opposed to seeing some black backrounds

Requirements
Must have
• Logo/website address with design on front only - www.brellstone-example.com (logo attached)
• Back:
• Name/Title/Company Address/Phone/email address
Nice to have
• Cool design
Should not have
• Nothing gimmicky like Fire or Water - since we are a Fire Protection company - it has all been done

```html
<!DOCTYPE html>
<html lang="en">
<head>
<meta charset="utf-8">
<title>Brell Stone Company – Business Cards</title>
<link rel="stylesheet" href="https://fonts.googleapis.com/css2?family=Open+Sans:wght@400;600;800&display=swap">
<style>
  :root {
    --page-bg: #2a2a2c;
    --card-bg: #1f1f21;
    --card-edge: #2c2c2f;
    --silver: #c9c9cb;
    --text-light: #eeeeee;
    --accent-red: #e8503a;
    --divider: #6a6a6d;
  }
  html, body {
    margin: 0;
    padding: 0;
    width: 1200px;
    height: 874px;
    overflow: hidden;
    background: var(--page-bg);
    font-family: "Open Sans", Arial, sans-serif;
  }
  .sheet {
    position: relative;
    width: 1200px;
    height: 874px;
  }
  .card {
    position: absolute;
    left: 280px;
    width: 640px;
    height: 366px;
    border-radius: 22px;
    background: var(--card-bg);
    box-shadow: 0 0 0 1px var(--card-edge), 0 14px 30px rgba(0,0,0,0.45);
  }
  .card-front { top: 48px; }
  .card-back  { top: 460px; }

  /* Front */
  .brand {
    position: absolute;
    left: 0;
    right: 0;
    top: 130px;
    text-align: center;
    font-weight: 800;
    font-size: 64px;
    letter-spacing: -1px;
    color: var(--silver);
    line-height: 1;
  }
  .brand-mark {
    display: inline-block;
    width: 16px;
    height: 16px;
    margin-left: 10px;
    background: var(--silver);
    vertical-align: middle;
  }

  /* Back */
  .identity {
    position: absolute;
    right: 340px;
    top: 184px;
    text-align: right;
    color: var(--text-light);
    font-size: 14px;
    line-height: 1.35;
  }
  .identity .person-name {
    color: var(--accent-red);
    font-weight: 600;
    font-size: 21px;
    margin-bottom: 2px;
  }
  .divider {
    position: absolute;
    left: 316px;
    top: 190px;
    width: 1px;
    height: 92px;
    background: var(--divider);
  }
  .contacts {
    position: absolute;
    left: 334px;
    top: 204px;
    margin: 0;
    padding: 0;
    list-style: none;
    color: var(--text-light);
    font-size: 14px;
  }
  .contacts li {
    display: flex;
    align-items: center;
    gap: 10px;
    height: 21px;
  }
  .contacts svg {
    width: 13px;
    height: 13px;
    fill: var(--accent-red);
    flex: none;
  }
</style>
</head>
<body>
<main class="sheet">
  <section class="card card-front" aria-label="Card front">
    <div class="brand">brellstone inc.<span class="brand-mark"></span></div>
  </section>

  <section class="card card-back" aria-label="Card back">
    <div class="identity">
      <div class="person-name">Aaron Vale</div>
      <div class="person-title">CEO/Founder</div>
      <div class="address-line">48 Harbor Lane</div>
      <div class="address-line">Millbrook, NY 10000</div>
    </div>
    <div class="divider"></div>
    <ul class="contacts">
      <li>
        <svg viewBox="0 0 16 16" aria-hidden="true"><path d="M3.5 1l3 3-1.8 1.8c.9 2 2.5 3.6 4.5 4.5L11 8.5l3 3-2 2.5C6.5 13.5 2.5 9.5 1 3.5z"/></svg>
        <span>(555) 010-2468</span>
      </li>
      <li>
        <svg viewBox="0 0 16 16" aria-hidden="true"><path d="M4 1h8v4H4zM1 6h14v6h-3v3H4v-3H1zM5 10v4h6v-4z"/></svg>
        <span>(555) 010-2469</span>
      </li>
      <li>
        <svg viewBox="0 0 16 16" aria-hidden="true"><path d="M1 3h14v1.2L8 9 1 4.2zM1 5.8l7 4.8 7-4.8V13H1z"/></svg>
        <span>info@brellstone-example.com</span>
      </li>
      <li>
        <svg viewBox="0 0 16 16" aria-hidden="true"><path d="M8 1a7 7 0 100 14A7 7 0 008 1zm0 2c.8 0 1.7 2 1.9 4H6.1C6.3 5 7.2 3 8 3zM6.1 9h3.8c-.2 2-1.1 4-1.9 4s-1.7-2-1.9-4zM3.1 7h1.9c.1-1.3.4-2.5.9-3.4A5 5 0 003.1 7zm0 2a5 5 0 002.8 3.4c-.5-.9-.8-2.1-.9-3.4zm7.9 0c-.1 1.3-.4 2.5-.9 3.4A5 5 0 0012.9 9zm1.9-2a5 5 0 00-2.8-3.4c.5.9.8 2.1.9 3.4z"/></svg>
        <span>www.brellstone-example.com</span>
      </li>
    </ul>
  </section>
</main>
</body>
</html>
```